Home decoration company - sustainable wall panels

- I would need you to design 5-10 pages for my client's website.
- The design should have details of wall panels that are being sold on the website - movelterra.com.
- It should have wood + sustainability branding.
- please focus on using shapes of products that are being sold on the website and use them as design for branding

See more here
https://sheets.quorvix.net/d/7kpRtW2nLqZ8bYhMfGcVdXsJ4eTuA9wN3oHiKy5BzPl/edit?usp=sharing

Target Market(s)

people who are want sustainable home/business wall decor

Industry/Entity Type

Interior Decoration

Logo Text

Movel Terra (for favicon, "MT")

Number of Pages Required

5+ page

Font styles to use
Serif
Sans Serif

Requirements
Must have
• - details of products that are being sold on the website movelterra.com (you will see there are different wall panel shapes)
- great creative design ideas
- follow instructions from here https://sheets.quorvix.net/d/7kpRtW2nLqZ8bYhMfGcVdXsJ4eTuA9wN3oHiKy5BzPl/edit?usp=sharing
- the design must be at least 2 levels above the current one on movelterra.com
- use photos from here https://files.quorvix.net/folders/5tWmQeRb8YuNc2XkLpAsDv3ZhGj7FiO-?usp=sharing
Nice to have
• - it would be nice if you would give your own creative suggestions
Should not have
• - should not look like it's a 1990s website

```html
<!DOCTYPE html>
<html lang="en">
<head>
<meta charset="utf-8">
<title>Wall Paneling – Movel Terra</title>
<link href="https://fonts.googleapis.com/css2?family=Oswald:wght@500;600;700&family=Poppins:wght@300;400;500;600;700&display=swap" rel="stylesheet">
<style>
:root{
  --brown-dark:#3b1d05;
  --brown:#4a2608;
  --brown-btn:#7a3d0a;
  --accent:#a3520f;
  --star:#f0a21e;
  --text:#4a4a4a;
  --heading:#2d1604;
  --white:#fff;
}
*{box-sizing:border-box;margin:0;padding:0}
html,body{width:1200px;height:3105px;overflow:hidden;background:#fff}
body{font-family:'Poppins',sans-serif;color:var(--text);position:relative}
.abs{position:absolute}
.h-cond{font-family:'Oswald',sans-serif;font-weight:600;text-transform:uppercase;color:var(--heading);letter-spacing:-.5px}

.topbar{left:0;top:0;width:1200px;height:29px;background:var(--brown-dark);color:#fff;font-size:11px;display:flex;align-items:center;justify-content:space-between;padding:0 88px}
.topbar .info{display:flex;gap:22px;align-items:center}
.topbar .info span{display:flex;align-items:center;gap:6px}
.nav{left:0;top:29px;width:1200px;height:70px;background:#fff;border-bottom:1px solid #eee}
.brand{left:88px;top:22px;font-weight:500;color:var(--accent);font-size:18px;letter-spacing:3px;display:flex;align-items:center;gap:8px}
.brand i{display:block;width:14px;height:14px;background:var(--accent)}
.menu{right:88px;top:0;height:70px;display:flex;align-items:center;gap:27px;font-family:'Oswald',sans-serif;font-weight:500;font-size:13px;text-transform:uppercase;color:#2a1a0a}
.menu .active{color:var(--accent)}

.hero{left:0;top:99px;width:1200px;height:217px;background:linear-gradient(90deg,#5b3c22 0%,#8a6040 30%,#6b4a2f 55%,#a06b3a 80%,#5e3a1c 100%)}
.hero::after{content:"";position:absolute;inset:0;background:rgba(0,0,0,.3)}
.hero-text{left:0;top:180px;width:1200px;text-align:center;color:#fff;z-index:2}
.hero-text h1{font-family:'Oswald',sans-serif;font-weight:600;font-size:38px;line-height:44px;color:#fff}
.hero-text p{font-weight:600;font-size:19px;margin-top:2px}

.how{left:0;top:415px;width:1200px;text-align:center}
.how h2{font-size:37px;line-height:44px}
.how p{width:800px;margin:14px auto 0;font-size:14.5px;line-height:21px;color:#555}

.origin-title{left:0;top:612px;width:1200px;text-align:center;font-size:33px;line-height:40px}
.band{left:87px;top:845px;width:1022px;height:461px;background:var(--brown)}
.pic1{left:135px;top:687px;width:302px;height:344px;background:linear-gradient(160deg,#b08a5c,#8a6a45 60%,#6d5336)}
.pic2{left:452px;top:687px;width:301px;height:345px;background:linear-gradient(160deg,#d9b992,#c79b6b 60%,#8a7a62)}
.pic3{left:765px;top:687px;width:302px;height:345px;background:linear-gradient(180deg,#9a7a5a 0%,#7a5e42 55%,#2a2522 70%,#d2661f 85%,#b95a1c 100%)}
.dots{position:absolute;bottom:22px;left:50%;transform:translateX(-50%);display:flex;gap:4px}
.dots b{width:8px;height:8px;border-radius:50%;background:rgba(255,255,255,.6)}
.dots b.on{background:#fff}
.step{color:#fff;font-size:13px;line-height:19.5px}
.step h3{font-family:'Oswald',sans-serif;font-weight:600;font-size:33px;line-height:40px;color:#fff;margin-bottom:4px;letter-spacing:-.5px;text-transform:uppercase}
.step p+p{margin-top:10px}
.s1{left:134px;top:1058px;width:285px}
.s2{left:451px;top:1055px;width:295px}
.s2 h3{margin-bottom:6px}
.s3{left:768px;top:1055px;width:305px}
.s3 h3{margin-bottom:14px}

.prod-img{left:646px;top:1396px;width:465px;height:564px;background:linear-gradient(90deg,#5a3b22 0%,#7a5433 28%,#e8c98a 32%,#9a6d42 50%,#6b7a7a 70%,#a3683c 100%)}
.prod{left:87px;top:1497px;width:510px}
.prod h2{font-size:37px;line-height:46px}
.prod .rating{font-weight:600;font-size:17px;color:#222;margin-top:2px;display:flex;align-items:center;gap:6px;letter-spacing:.5px}
.prod p{font-size:14px;line-height:21px;color:#555;margin-top:8px}
.prod .price{font-family:'Oswald',sans-serif;font-weight:600;font-size:27px;color:var(--accent);margin-top:10px}
.partner{left:88px;top:1768px;display:flex;align-items:center;gap:10px;font-weight:600;font-size:34px;line-height:44px;color:var(--heading)}
.partner i{display:block;width:16px;height:16px;background:var(--heading)}
.shop{left:88px;top:1844px;width:157px;height:44px;background:var(--brown-btn);color:#fff;font-weight:700;font-size:18px;display:flex;align-items:center;justify-content:center;letter-spacing:.5px}
.review{left:413px;top:1743px;width:333px;height:202px;background:#fff;box-shadow:0 4px 30px rgba(0,0,0,.12);padding:42px 36px 0}
.review p{font-size:14px;line-height:21.5px;color:#444}
.review .stars{margin-top:4px}
.review .name{font-weight:600;font-size:16px;color:var(--accent);margin-top:2px}
.review .arrows{position:absolute;right:32px;top:151px;display:flex;gap:18px}

.related-title{left:0;top:2068px;width:1200px;text-align:center;font-size:37px;line-height:46px}
.card{top:2139px;width:205px}
.card .thumb{height:262px;width:198px}
.card h4{font-family:'Oswald',sans-serif;font-weight:500;font-size:20px;line-height:23px;color:var(--heading);text-transform:uppercase;margin-top:15px;letter-spacing:-.4px;white-space:nowrap}
.card .stars{margin-top:7px}
.card .price{font-family:'Oswald',sans-serif;font-weight:500;font-size:18px;color:var(--heading);margin-top:4px}
.c1{left:152px}.c1 .thumb{background:linear-gradient(180deg,#8d6c4c,#b58d62 50%,#7a5d40)}
.c2{left:387px}.c2 .thumb{background:linear-gradient(135deg,#d6cabb,#8f7f6c 50%,#c8b9a5)}
.c3{left:618px}.c3 .thumb{background:linear-gradient(180deg,#6a5038,#9c7a56 50%,#4f3b29)}
.c4{left:851px}.c4 .thumb{background:linear-gradient(160deg,#6d6256,#8e8273 50%,#4d443b)}

.footer{left:0;top:2609px;width:1200px;height:496px;background:radial-gradient(circle at 20% 40%,#f2f2f2,#e6e6e6 70%)}
.f-brand{left:92px;top:2770px;font-weight:500;font-size:34px;line-height:44px;letter-spacing:6px;color:var(--brown);display:flex;align-items:center;gap:12px}
.f-brand i{display:block;width:30px;height:30px;background:var(--brown)}
.f-col h5{font-family:'Oswald',sans-serif;font-weight:500;font-size:23px;color:var(--heading);text-transform:uppercase;line-height:30px;margin-bottom:8px}
.f-col li{list-style:none;font-size:13px;line-height:24px;color:#555}
.f-nav{left:351px;top:2718px}
.f-contact{left:542px;top:2718px;width:240px}
.f-contact li{display:flex;gap:8px;line-height:20px;margin-bottom:4px}
.f-contact li svg{flex:none;margin-top:4px}
.social{display:flex;gap:14px;margin-top:14px}
.social i{display:block;width:15px;height:15px;background:var(--accent);border-radius:3px}
.social i.round{border-radius:50%}
.f-form{left:827px;top:2718px;width:248px}
.f-form .field{background:#ddd;height:30px;margin-bottom:3px;font-size:11px;color:#555;padding:8px 16px}
.f-form .msg{height:100px;margin-top:4px}
.f-form .submit{width:93px;height:30px;background:var(--brown-btn);color:#fff;font-weight:600;font-size:12px;display:flex;align-items:center;justify-content:center;margin-top:8px;margin-left:3px}
.f-line{left:89px;top:3039px;width:1022px;height:1px;background:#ccc}
.copy{left:0;top:3061px;width:1200px;text-align:center;font-size:16px;color:#333}
.totop{left:1134px;top:3025px;width:34px;height:34px;border-radius:50%;background:var(--brown-dark);display:flex;align-items:center;justify-content:center}
</style>
</head>
<body>

<header class="abs topbar">
  <span>Ordering larger quantities? Call us.</span>
  <div class="info">
    <span><svg width="10" height="10" viewBox="0 0 24 24"><path fill="#d9781f" d="M6.6 10.8a15 15 0 0 0 6.6 6.6l2.2-2.2c.3-.3.7-.4 1-.2 1.1.4 2.3.6 3.6.6.6 0 1 .4 1 1V20c0 .6-.4 1-1 1A17 17 0 0 1 3 4c0-.6.4-1 1-1h3.5c.6 0 1 .4 1 1 0 1.2.2 2.4.6 3.6.1.3 0 .7-.2 1z"/></svg>phone number : &nbsp;+1 555 014 7720</span>
    <span><svg width="11" height="9" viewBox="0 0 24 18"><path fill="#d9781f" d="M0 0h24v18H0zM2 2l10 7 10-7z"/></svg>Email : hello@movelterra.com, orders@movelterra.com</span>
  </div>
</header>

<nav class="abs nav">
  <div class="abs brand"><i></i>MOVEL TERRA</div>
  <div class="abs menu">
    <span>Home</span><span class="active">Wall Paneling</span><span>Door</span><span>Cutting Boards</span><span>Table Tops</span><span>About Us</span><span>Contact Us</span>
  </div>
</nav>

<section class="abs hero" role="img" aria-label="Photo of visitors at a trade booth lined with reclaimed wood wall panels"></section>
<div class="abs hero-text">
  <h1>WALL PANELING</h1>
  <p>100% Sustainable. 100% Hand Crafted. 100% Unique.</p>
</div>

<section class="abs how">
  <h2 class="h-cond">How It's Made</h2>
  <p>We search the shores of East Java for teak fishermen's boats and barns which are no longer usable and transform them into panels.This also provides local fisherman a sustainable income. Every panel is unique given they are expertly handmade using different combinations of boat pieces and reclaimed wood.</p>
</section>

<h2 class="abs h-cond origin-title">Movel Terra Wall Panel Origin Story</h2>
<div class="abs band"></div>

<div class="abs pic1" role="img" aria-label="Close-up of reclaimed wood planks"><div class="dots"><b></b><b class="on"></b><b></b><b></b></div></div>
<div class="abs pic2" role="img" aria-label="Stacked cardboard boxes of packed panels"><div class="dots"><b></b><b class="on"></b><b></b><b></b></div></div>
<div class="abs pic3" role="img" aria-label="Bar interior with a wood round panel wall and orange chairs"><div class="dots"><b></b><b class="on"></b><b></b><b></b></div></div>

<div class="abs step s1">
  <h3>Reclaim</h3>
  <p>We search the shores of East Java for teak-wood fishermen's boats and barns which are no longer usable andtransform them into gorgeous and durable décor for your home or business.slider</p>
  <p>Using irreparable boats and barns not only provides raw material, it also provides local fisherman a sustainableincome.</p>
</div>
<div class="abs step s2">
  <h3>Recycle</h3>
  <p>Each of these unique boats or pieces is pains-takingly dismantled by master craftsmen. The wood is then dried for 8-12 months to ensure exceptional durability.</p>
</div>
<div class="abs step s3">
  <h3>Create</h3>
  <p>Every panel is unique given they are expertly handmade using different combinations of boat pieces and reclaimedwood.</p>
  <p>Quality is our top priority. All our products under-go rigorous inspection before packaging.</p>
</div>

<div class="abs prod-img" role="img" aria-label="Lit interior wall clad in multicoloured reclaimed wood boards"></div>
<section class="abs prod">
  <h2 class="h-cond">Strata S Panel TP-101</h2>
  <div class="rating">RATING: &nbsp;5.00 <svg width="15" height="15" viewBox="0 0 24 24"><path fill="#f0a21e" d="M12 2l3 7h7l-5.6 4.3 2.1 7.2L12 16.3 5.5 20.5l2.1-7.2L2 9h7z"/></svg></div>
  <p>GreenBuild: these boards may help qualify your project for GreenBuild points MR 4.1 &amp; 4.2 (Recycled Content) and EQ 4.4 (low VOC emission)</p>
  <p>TCF Certified: These products have a Chain-of-Custody TCF certification as well as the Timber Legality Verification by the CVT authority.</p>
  <p>Plank dimensions: L 47.75 x W 11.75 x T 0.75<br>Eco-conscious manufacturing.</p>
  <div class="price">$5.99</div>
</section>
<div class="abs partner">Casaloft<i></i></div>
<div class="abs shop">SHOP NOW</div>

<div class="abs review">
  <p>Lorem Ipsum is simply dummy text of the printing and typesetting industry. Lorem Ipsum has been the industry's standard dummy text.</p>
  <div class="stars">
    <svg width="84" height="14" viewBox="0 0 90 15"><g fill="#f0a21e"><path id="st" d="M7.5 0l2 4.8h5l-4 3 1.5 5-4.5-3-4.5 3 1.5-5-4-3h5z"/><use href="#st" x="18"/><use href="#st" x="36"/><use href="#st" x="54"/><use href="#st" x="72"/></g></svg>
  </div>
  <div class="name">Ada Brennan</div>
  <div class="arrows">
    <svg width="10" height="14" viewBox="0 0 10 14"><path d="M8 1L2 7l6 6" stroke="#222" stroke-width="2" fill="none"/></svg>
    <svg width="10" height="14" viewBox="0 0 10 14"><path d="M2 1l6 6-6 6" stroke="#222" stroke-width="2" fill="none"/></svg>
  </div>
</div>

<h2 class="abs h-cond related-title">Related Products</h2>
<svg width="0" height="0" class="abs"><defs><g id="five" fill="#f0a21e"><path id="s5" d="M7.5 0l2 4.8h5l-4 3 1.5 5-4.5-3-4.5 3 1.5-5-4-3h5z"/><use href="#s5" x="18"/><use href="#s5" x="36"/><use href="#s5" x="54"/><use href="#s5" x="72"/></g></defs></svg>
<article class="abs card c1"><div class="thumb" role="img" aria-label="Brushed wood strip panel texture"></div><h4>Driftwood Brushed<br>TP-202</h4><div class="stars"><svg width="84" height="14" viewBox="0 0 90 15"><use href="#five"/></svg></div><div class="price">$25.00</div></article>
<article class="abs card c2"><div class="thumb" role="img" aria-label="Wood prism relief panel texture"></div><h4>Driftwood Prism<br>TP-208</h4><div class="stars"><svg width="84" height="14" viewBox="0 0 90 15"><use href="#five"/></svg></div><div class="price">$25.00</div></article>
<article class="abs card c3"><div class="thumb" role="img" aria-label="Small wood block mosaic panel texture"></div><h4>Driftwood Mosaic<br>TP-209</h4><div class="stars"><svg width="84" height="14" viewBox="0 0 90 15"><use href="#five"/></svg></div><div class="price">$25.00</div></article>
<article class="abs card c4"><div class="thumb" role="img" aria-label="Carved wood relief panel"></div><h4>Driftwood Relief<br>TP-210</h4><div class="stars"><svg width="84" height="14" viewBox="0 0 90 15"><use href="#five"/></svg></div><div class="price">$25.00</div></article>

<footer class="abs footer" role="img" aria-label="Faint wood ring texture background"></footer>
<div class="abs f-brand"><i></i>MOVEL<br>TERRA</div>
<div class="abs f-col f-nav">
  <h5>Navigation</h5>
  <ul><li>Home</li><li>Wall panels</li><li>Doors</li><li>Cutting boards</li><li>About us</li></ul>
</div>
<div class="abs f-col f-contact">
  <h5>Contact Us</h5>
  <ul>
    <li><svg width="11" height="11" viewBox="0 0 24 24"><path fill="#a3520f" d="M6.6 10.8a15 15 0 0 0 6.6 6.6l2.2-2.2c.3-.3.7-.4 1-.2 1.1.4 2.3.6 3.6.6.6 0 1 .4 1 1V20c0 .6-.4 1-1 1A17 17 0 0 1 3 4c0-.6.4-1 1-1h3.5c.6 0 1 .4 1 1 0 1.2.2 2.4.6 3.6.1.3 0 .7-.2 1z"/></svg>Phone number +1 555 014 7720</li>
    <li><svg width="12" height="9" viewBox="0 0 24 18"><path fill="#a3520f" d="M0 0h24v18H0zM2 2l10 7 10-7z"/></svg>Email us : hello@movelterra.com, orders@movelterra.com</li>
  </ul>
  <div class="social"><i></i><i></i><i class="round"></i></div>
</div>
<div class="abs f-col f-form">
  <h5>Contact Form</h5>
  <div class="field">Name</div>
  <div class="field">Email</div>
  <div class="field msg">Message</div>
  <div class="submit">SUBMIT</div>
</div>
<div class="abs f-line"></div>
<div class="abs copy">Copyright 2020 | All Rights Reserved</div>
<div class="abs totop"><svg width="12" height="8" viewBox="0 0 12 8"><path d="M1 7l5-5 5 5" stroke="#fff" stroke-width="2" fill="none"/></svg></div>

</body>
</html>
```